creation of a business card design for a company specializing in the creation...

I would like to create a design for a professional business card on a black background and with the company's colors (I am attaching some files: including the logo in horizontal and centered format, I am also attaching a recent project design a T-shirt, this is the one I chose to give you an idea of my preferences.

we are in the process of developing a new website design, it is still in the development phase but it can be viewed at the following address: www.vantrelmo.be to give you other ideas about the company
you will see for yourself the subject of my main activity: company specializing in the construction of stairs

I would like a business card that stands out from the rest with a unique design

here is the informations
Name: Lucien Barthel
Function: Manager
Address: Rue Moulinet du Parc 42
7180 La Louvière
telephone: +32 468 219 804
email: info@rx7p.be
website: rx7p. be
social networks: Facebook, YouTube, TikTok, Instagram

Target Market(s)

customer who wants to have a beautiful staircase built

Industry/Entity Type

contruction d'escalier

Contact Information for Business Card

Adresse. Numero de telephone, site web, le texte : "Createur d'escalier", logo recto-verso, icone des reseaux sociaux

Requirements
Must have
• the mention: Stair creator
Nice to have
• an illustration of a designer staircase
Should not have
• do not distort the logo

```html
<!DOCTYPE html>
<html lang="fr">
<head>
<meta charset="utf-8">
<title>RX7P – Carte de visite</title>
<link rel="stylesheet" href="https://fonts.googleapis.com/css2?family=Open+Sans:wght@400;600;700&display=swap">
<style>
  :root {
    --stage: #242424;
    --card: #1e1f22;
    --accent: #6a9fc4;
    --accent-dark: #4f7f9f;
    --text: #f2f2f2;
    --pattern-dark: #17181b;
    --pattern-light: #8a8d92;
  }
  * { margin: 0; padding: 0; box-sizing: border-box; }
  html, body {
    width: 1200px; height: 780px; overflow: hidden;
    background: var(--stage);
    font-family: "Open Sans", Arial, sans-serif;
    color: var(--text);
  }
  .canvas {
    position: relative; width: 1200px; height: 780px;
    display: flex; align-items: center; justify-content: center; gap: 40px;
  }
  .card {
    position: relative; width: 540px; height: 350px;
    background: var(--card);
    border-radius: 6px;
    overflow: hidden;
    box-shadow: 0 20px 40px rgba(0,0,0,.45);
  }

  /* Front */
  .brand-mark {
    position: absolute; left: 26px; top: 24px;
    display: flex; align-items: center; gap: 12px;
  }
  .brand-mark__dot {
    width: 52px; height: 52px; border-radius: 50%;
    background: var(--accent-dark);
  }
  .brand-mark__text { display: flex; flex-direction: column; }
  .brand-mark__name {
    font-weight: 600; font-size: 28px; letter-spacing: 2px; line-height: 1.1;
    color: var(--text);
  }
  .brand-mark__tagline {
    font-weight: 600; font-size: 11px; letter-spacing: 1.5px;
    text-transform: uppercase; color: var(--accent); margin-top: 2px;
  }
  .address {
    position: absolute; left: 28px; top: 104px;
    font-size: 16px; line-height: 1.35;
  }
  .contacts {
    position: absolute; left: 28px; top: 168px;
    list-style: none; font-size: 16px; line-height: 1.45;
  }
  .contacts li { display: flex; align-items: center; gap: 10px; }
  .contacts svg { width: 14px; height: 14px; fill: var(--accent); flex: none; }
  .identity {
    position: absolute; right: 74px; bottom: 40px; text-align: right;
  }
  .identity__name {
    font-weight: 700; font-size: 29px; color: var(--accent); line-height: 1.1;
  }
  .identity__role { font-size: 18px; line-height: 1.3; }
  .accent-bars { position: absolute; right: 0; bottom: 38px; }
  .accent-bars span {
    display: block; height: 15px; margin-left: auto; margin-bottom: 3px;
    background: var(--accent);
  }
  .accent-bars span:nth-child(1) { width: 50px; }
  .accent-bars span:nth-child(2) { width: 40px; }
  .accent-bars span:nth-child(3) { width: 30px; opacity: .8; }

  /* Back */
  .pattern-field {
    position: absolute; inset: 0;
    background: linear-gradient(115deg, var(--pattern-dark) 0%, var(--pattern-dark) 45%, #3a3c40 70%, var(--pattern-light) 100%);
  }
  .back-brand {
    position: absolute; left: 50%; top: 58%;
    transform: translateX(-50%);
    display: flex; align-items: center; gap: 12px;
    background: var(--card); padding: 8px 16px; border-radius: 4px;
  }
  .back-brand__square { width: 26px; height: 26px; background: var(--accent); }
  .back-brand__name { font-weight: 600; font-size: 28px; letter-spacing: 3px; color: var(--text); }
</style>
</head>
<body>
<main class="canvas">

  <section class="card card--front" aria-label="Recto de la carte">
    <div class="brand-mark">
      <span class="brand-mark__dot"></span>
      <div class="brand-mark__text">
        <span class="brand-mark__name">RX7P</span>
        <span class="brand-mark__tagline">Créateur d'escalier</span>
      </div>
    </div>

    <p class="address">Rue Moulinet du Parc 42<br>7180 La Louvière</p>

    <ul class="contacts">
      <li>
        <svg viewBox="0 0 24 24" aria-hidden="true"><path d="M6.6 10.8a15.1 15.1 0 0 0 6.6 6.6l2.2-2.2a1 1 0 0 1 1-.25 11.4 11.4 0 0 0 3.6.57 1 1 0 0 1 1 1V20a1 1 0 0 1-1 1A17 17 0 0 1 3 4a1 1 0 0 1 1-1h3.5a1 1 0 0 1 1 1c0 1.25.2 2.45.57 3.6a1 1 0 0 1-.25 1z"/></svg>
        +32 468 219 804
      </li>
      <li>
        <svg viewBox="0 0 24 24" aria-hidden="true"><path d="M3 5h18v14H3zM4.5 6.5 12 12l7.5-5.5v-.2H4.5z"/></svg>
        info@rx7p.be
      </li>
      <li>
        <svg viewBox="0 0 24 24" aria-hidden="true"><path d="M12 2a10 10 0 1 0 0 20 10 10 0 0 0 0-20zm6.9 9h-3a15 15 0 0 0-1.4-6 8 8 0 0 1 4.4 6zM12 4c.9 1.2 1.8 3.8 1.9 7h-3.8c.1-3.2 1-5.8 1.9-7zM9.5 5a15 15 0 0 0-1.4 6h-3a8 8 0 0 1 4.4-6zm-4.4 8h3a15 15 0 0 0 1.4 6 8 8 0 0 1-4.4-6zM12 20c-.9-1.2-1.8-3.8-1.9-7h3.8c-.1 3.2-1 5.8-1.9 7zm2.5-1a15 15 0 0 0 1.4-6h3a8 8 0 0 1-4.4 6z"/></svg>
        www.rx7p. be
      </li>
    </ul>

    <div class="identity">
      <p class="identity__name">Lucien Barthel</p>
      <p class="identity__role">Manager</p>
    </div>

    <div class="accent-bars" aria-hidden="true"><span></span><span></span><span></span></div>
  </section>

  <section class="card card--back" aria-label="Verso de la carte">
    <div class="pattern-field" role="img" aria-label="Motif répété en diagonale du symbole de la marque, noir sur noir, avec reflet argenté vers la droite"></div>
    <div class="back-brand">
      <span class="back-brand__square"></span>
      <span class="back-brand__name">RX7P</span>
    </div>
  </section>

</main>
</body>
</html>
```